4th Generation Family Business Needs a New Card Design!

We are a family owned 4th Generation company. We are based in the Sydney, Australia area and we are desperately in need of a more modern and classy card. We are monumental masons who design, supply & erect lasting memorials throughout cemeteries in Sydney. Our customers are normally in a period of grieving. I have attached logo files that will need to be implemented on the card. Company was established 1935. Australian Owned and Operated. Card needs to be designed to PIXO.com specification.

Target Market(s)

Our target market is based upon people that a grieving for family members that have passed away. We also deal with alot of companies that own and operate cemeteries.

Industry/Entity Type

Business

Contact Information for Business Card

Simon Harcourt, Operations Manager, 0417293086, simon@harcourtmemorials.com.au
Lewis Harcourt, Director, 0491630572, lewis@harcourtmemorials.com.au
Phone # 02 9561 3048
Website: www.harcourtmemorials.com.au
Address: Suite 17, 8 Palfrey Lane, West Carlow, Sydney NSW 2156

Font styles to use
Serif
Decorative
Script

Requirements
Must have
• Would like to see the logo nicely implemented with a modern design. Embossed lettering would be a nice additive.

```html
<!DOCTYPE html>
<html lang="en">
<head>
<meta charset="utf-8">
<title>Harcourt Memorials – Business Card</title>
<link rel="stylesheet" href="https://fonts.googleapis.com/css2?family=Cinzel:wght@400;600&family=EB+Garamond:wght@400&display=swap">
<style>
  :root {
    --backdrop: #3b3532;
    --card: #e9eaea;
    --card-back: #eef0f0;
    --ink: #1f1d1e;
    --ink-soft: #3a3a3c;
    --gold: #eec33f;
    --gold-text: #c9a23a;
    --band-dark: #252223;
    --silver: #8d9093;
  }
  * { margin: 0; padding: 0; box-sizing: border-box; }
  html, body { width: 1200px; height: 769px; overflow: hidden; }
  body { background: var(--backdrop); position: relative; font-family: "EB Garamond", serif; }

  .card {
    position: absolute;
    top: 230px;
    width: 540px;
    height: 309px;
    overflow: hidden;
    box-shadow: 0 6px 18px rgba(0,0,0,0.35);
  }
  .card--front { left: 40px; background: var(--card); }
  .card--back { left: 620px; background: var(--card-back); }

  /* Front: contact block (ends above the bottom band) */
  .contact { position: absolute; left: 40px; top: 84px; color: var(--ink-soft); }
  .contact__name { font-family: "Cinzel", serif; font-weight: 600; font-size: 19px; line-height: 22px; color: var(--ink); letter-spacing: 0.5px; }
  .contact__title { font-family: "Cinzel", serif; font-size: 12.5px; line-height: 16px; color: var(--gold-text); letter-spacing: 0.6px; margin-top: 1px; }
  .contact__address { font-size: 13.5px; line-height: 16px; margin-top: 12px; }
  .contact__list { list-style: none; margin-top: 12px; font-size: 13.5px; line-height: 17px; }
  .contact__list li { display: flex; align-items: center; gap: 8px; white-space: nowrap; }
  .contact__list svg { width: 11px; height: 11px; flex: none; fill: var(--ink); }

  /* Front: wordmark */
  .wordmark { position: absolute; text-align: center; font-family: "Cinzel", serif; font-weight: 600; color: var(--ink); }
  .card--front .wordmark { left: 300px; top: 122px; width: 220px; }
  .wordmark__line { display: block; font-size: 34px; line-height: 36px; letter-spacing: 1px; }
  .wordmark__sub { display: block; font-size: 15px; letter-spacing: 3px; line-height: 20px; }

  /* Front: bottom bands */
  .band { position: absolute; bottom: 0; }
  .band--dark { left: 0; width: 318px; height: 14px; background: var(--band-dark); }
  .band--gold { left: 318px; right: 0; height: 22px; background: var(--gold); }

  /* Back */
  .card--back .wordmark { left: 0; width: 100%; top: 105px; color: var(--silver); }
  .social-row { position: absolute; left: 0; width: 100%; top: 200px; display: flex; justify-content: center; gap: 8px; }
  .social-row span { width: 11px; height: 11px; border-radius: 50%; background: var(--ink-soft); }
</style>
</head>
<body>

<section class="card card--front" aria-label="Business card front">
  <div class="contact">
    <p class="contact__name">Simon Harcourt</p>
    <p class="contact__title">Operations Manager</p>
    <p class="contact__address">Suite 17<br>8 Palfrey Lane, West Carlow<br>Sydney NSW 2156</p>
    <ul class="contact__list">
      <li><svg viewBox="0 0 12 12" aria-hidden="true"><path d="M2.5 0.8l2 2.2-1 1.3c.6 1.5 1.7 2.6 3.2 3.2l1.3-1 2.2 2-1 2.1C5.5 10.6 1.4 6.5 0.4 2.2z"/></svg>02 9561 3048</li>
      <li><svg viewBox="0 0 12 12" aria-hidden="true"><path d="M3 0h6v12H3zM4 1.5v8h4v-8z"/></svg>0417293086</li>
      <li><svg viewBox="0 0 12 12" aria-hidden="true"><path d="M0 2h12v8H0zM1 3.2v.3l5 3.2 5-3.2v-.3z"/></svg>simon@harcourtmemorials.com.au</li>
      <li><svg viewBox="0 0 12 12" aria-hidden="true"><circle cx="6" cy="6" r="5.5"/></svg>www.harcourtmemorials.com.au</li>
    </ul>
  </div>

  <div class="wordmark">
    <span class="wordmark__line">Harcourt</span>
    <span class="wordmark__sub">Memorials</span>
  </div>

  <div class="band band--dark"></div>
  <div class="band band--gold"></div>
</section>

<section class="card card--back" aria-label="Business card back">
  <div class="wordmark">
    <span class="wordmark__line">Harcourt</span>
    <span class="wordmark__sub">Memorials</span>
  </div>
  <div class="social-row" aria-hidden="true">
    <span></span><span></span><span></span><span></span><span></span><span></span><span></span>
  </div>
</section>

</body>
</html>
```